13 Varno - new website design project

Our company Varno Electrical is developing a new lead generation website focused on Electrical, LED Lighting and Solar Power. We need a high converting website.

Example of our current website is www.varnoelectrical-example.com.au You can take content from this website for this new design. Our colours are red, black and white. For our new website we would like to promote Varno, Spark Every Day. Please listen to the jingle.

The below link is the company jingle that we have developed.
http://www.tunecraftdemo.com.au/vrn-tc-v1/

The key for this brief is to generate leads for Electrical, LED Lighting (for commercial) and Solar Power & Storage.

Target Market(s)

Business owners in Melbourne Victoria

Number of Pages Required

4 page

Colors
ec1f27
ffffff

Requirements
Must have
• This page must be clean, be in line with company branding and a high converting lead website.

```html
<!DOCTYPE html>
<html lang="en">
<head>
<meta charset="utf-8">
<title>Varno Electrical</title>
<link rel="stylesheet" href="https://fonts.googleapis.com/css2?family=Roboto:wght@400;500;700&family=Open+Sans:wght@400;700;800&family=Roboto+Condensed:wght@400&display=swap">
<style>
  :root{
    --nav-bg:#5f6064;
    --hero-dark:#5d5e62;
    --hero-mid:#6f7074;
    --hero-light:#9a9ba0;
    --brand-red:#ec1f27;
    --band-red-light:#f27a7c;
    --bulb-yellow:#f5c000;
    --white:#ffffff;
    --ink:#222222;
    --page:#f2f2f2;
  }
  *{box-sizing:border-box;margin:0;padding:0}
  html,body{width:1200px;height:676px;overflow:hidden;background:var(--page)}
  body{font-family:"Roboto",sans-serif;color:var(--white)}
  .site{width:1200px;height:676px;position:relative;overflow:hidden}

  .header{position:absolute;top:0;left:0;right:0;height:72px;
    background:var(--nav-bg);border-bottom:1px solid rgba(255,255,255,.35);
    display:flex;align-items:center;padding:0 40px;z-index:2}
  .brand{display:flex;align-items:center;gap:10px;font-weight:700;font-size:30px;color:var(--white);width:260px}
  .brand-dot{width:14px;height:14px;border-radius:50%;background:var(--white)}
  .nav{display:flex;gap:38px;margin-left:40px;font-size:15px;font-weight:500;letter-spacing:.2px}
  .actions{margin-left:auto;display:flex;gap:8px}
  .btn{font-size:12px;padding:7px 12px;border-radius:16px;font-weight:500}
  .btn-outline{border:1px solid var(--white);color:var(--white)}
  .btn-solid{background:var(--white);color:var(--ink)}

  .hero{position:absolute;top:73px;left:0;right:0;height:405px;
    background:linear-gradient(180deg,var(--hero-dark),var(--hero-mid))}
  .hero::before{content:"";position:absolute;inset:0;
    background:linear-gradient(135deg,#7a7b80,var(--hero-light));
    clip-path:polygon(445px 0,100% 0,100% 100%,830px 100%)}
  .hero-copy{position:absolute;left:60px;top:135px;width:530px;text-align:center}
  .hero-kicker{font-family:"Roboto Condensed",sans-serif;font-size:30px;display:flex;
    align-items:center;justify-content:center;gap:16px}
  .hero-kicker .rule{width:46px;height:9px;
    background:repeating-linear-gradient(120deg,#d8d8d8 0 2px,transparent 2px 5px)}
  .hero-title{font-family:"Open Sans",sans-serif;font-weight:800;font-size:70px;
    letter-spacing:1px;line-height:1;margin-top:6px;text-shadow:0 3px 4px rgba(0,0,0,.35)}
  .hero-phone{font-size:21px;letter-spacing:1px;margin-top:10px}
  .hero-illustration{position:absolute;left:820px;top:25px;width:270px;height:290px;border-radius:8px;
    background:radial-gradient(ellipse at 50% 45%,rgba(245,192,0,.35),rgba(245,192,0,.08) 65%,transparent 80%)}

  .welcome{position:absolute;top:478px;left:0;right:0;height:112px;
    background:linear-gradient(90deg,var(--brand-red),var(--band-red-light));text-align:center;padding-top:10px}
  .welcome h1{font-size:21px;font-weight:700}
  .welcome .divider{margin:14px 60px 12px;border-top:1px dashed rgba(255,255,255,.85)}
  .welcome p{font-size:12px;line-height:1.5;width:1000px;margin:0 auto}

  .services{position:absolute;top:590px;left:0;right:0;bottom:0;background:#f6f6f6;text-align:center}
  .services-photo{position:absolute;top:0;width:200px;height:86px;
    background:radial-gradient(ellipse at 40% 60%,#e0e0e0,#f6f6f6 70%)}
  .services h2{position:relative;color:var(--ink);font-size:21px;font-weight:500;padding-top:14px}
  .services h2 span{color:var(--brand-red);font-weight:700}
  .services .divider{position:relative;margin:10px 40px 0;border-top:1px dashed var(--brand-red)}
</style>
</head>
<body>
<div class="site">
  <header class="header">
    <div class="brand"><span class="brand-dot"></span>Varno</div>
    <nav class="nav">
      <span>HOME</span><span>ABOUT US</span><span>SERVICES</span><span>OUR WORK</span><span>CONTACT</span>
    </nav>
    <div class="actions">
      <span class="btn btn-outline">Log In</span>
      <span class="btn btn-solid">Request a Quote</span>
    </div>
  </header>

  <section class="hero">
    <div class="hero-copy">
      <div class="hero-kicker"><span class="rule"></span>DO YOU NEED A NEW<span class="rule"></span></div>
      <div class="hero-title">ELECTRICIAN?</div>
      <div class="hero-phone">Call Varno Electric at (13 7290)</div>
    </div>
    <div class="hero-illustration" role="img" aria-label="Yellow line illustration of a glowing light bulb"></div>
  </section>

  <section class="welcome">
    <h1>Welcome to Varno Electrical</h1>
    <div class="divider"></div>
    <p>Varno Electrical was formed to be an expert Electricity Contracting Company providing services to all Residential and Commercial Customers. With over 10 years of experience, Varno Electrical has developed a highly-experienced team of professionals that ensure all our customer expectations are met.</p>
  </section>

  <section class="services">
    <div class="services-photo" role="img" aria-label="Energy-saving light bulb photo" style="left:40px"></div>
    <div class="services-photo" role="img" aria-label="Energy-saving light bulb photo" style="left:480px"></div>
    <div class="services-photo" role="img" aria-label="Energy-saving light bulb photo" style="left:900px"></div>
    <h2>Our <span>Services</span></h2>
    <div class="divider"></div>
  </section>
</div>
</body>
</html>
```